Non Profit Company Looking For New Website

The website for Fernvale Quillstone Heritage Society should offer the viewer beautiful photos that inspire condifence and joy and tap into our love of horses.

We would like to see a website that displays trust, quality and confidence. Needs to be responsive and mobile friendly for all browsers and coded for both Android & IOS.

READ ATTACHED WEBSITE TEMPLATE FOR COMPLETE DETAILS ON WHAT WE ARE LOOKING FOR.

Looking for recommmendations if we should use WordPress/WooCommerce for site or Wordpress with Shopify Plug in or just Shopify.

Must be both desktop and mobile friendly with fast page load speed. Need the ability to edit ourselves.

Industry/Entity Type

Non Profit

Coding

Coded - Design and coding required

Number of Pages Required

5+ page

Requirements
Must have
• We would like to see a website that displays trust, quality and confidence. Needs to be responsive and mobile friendly for all browsers and coded for both Android & IOS.

Looking for recommendations if we should use WordPress/WooCommerce for site or Wordpress with Shopify Plug in or just Shopify.

Logo Colour:
Pantone 7621 C

READ TEMPLATE THAT IS ATTACHED
Nice to have
• Like look of this website as a sample:
https://www.quellbrimtorva.com/

Another similar non profit organization
https://pellaworthcindle.com/

```html
<!DOCTYPE html>
<html lang="en">
<head>
<meta charset="utf-8">
<title>Fernvale Quillstone Heritage Society</title>
<link href="https://fonts.googleapis.com/css2?family=Roboto+Slab:wght@500;700&family=Montserrat:wght@400;500;600;700&display=swap" rel="stylesheet">
<style>
:root{
  --red:#ad1a26;
  --gold:#f1b25c;
  --cream:#f4e7d8;
  --ink:#1c1c1c;
  --text:#2b2b2b;
  --footer:#1e1e1e;
  --line:#c9c1b7;
  --white:#ffffff;
}
*{box-sizing:border-box;margin:0;padding:0}
html,body{width:1200px;height:3618px;overflow:hidden}
body{position:relative;font-family:"Montserrat",sans-serif;color:var(--text);background:var(--white)}
.photo{position:absolute}

.btn{display:inline-flex;align-items:center;justify-content:center;gap:10px;height:40px;padding:0 18px;border-radius:22px;background:var(--gold);color:var(--ink);font-family:"Roboto Slab",serif;font-weight:700;font-size:15px;letter-spacing:.2px;white-space:nowrap}
.btn svg{width:14px;height:14px;flex:none}

/* hero */
.hero{position:absolute;left:0;top:0;width:1200px;height:552px;background:linear-gradient(100deg,#2a1f17 0%,#4a3322 38%,#7a5a3d 55%,#5b3a22 75%,#2b1a10 100%)}
.brand{position:absolute;left:150px;top:18px;width:130px;text-align:center;font-family:"Roboto Slab",serif;font-weight:700;color:var(--red);font-size:14px;line-height:17px}
.topbar{position:absolute;top:20px;left:525px;display:flex;align-items:center;gap:10px;color:#fff;font-size:14px;white-space:nowrap}
.topbar svg{width:14px;height:14px}
.topbar .dot{width:13px;height:13px;border-radius:50%;background:#fff;margin-left:16px}
.topbar .dot+.dot{margin-left:10px}
.nav{position:absolute;left:400px;top:77px;width:686px;height:35px;background:#141414;border-radius:18px;display:flex;align-items:center;justify-content:space-around;padding:0 14px;color:#fff;font-family:"Roboto Slab",serif;font-weight:700;font-size:15px;white-space:nowrap}
.hero-copy{position:absolute;left:112px;top:176px;width:480px;color:#fff}
.hero-copy h1{font-family:"Roboto Slab",serif;font-weight:700;font-size:42px;line-height:52px}
.hero-copy p{width:440px;font-size:14px;line-height:30px;margin:4px 0 14px}

/* about */
.about{position:absolute;left:0;top:552px;width:1200px;height:596px;background:var(--cream)}
.outline-frame{position:absolute;left:162px;top:80px;width:389px;height:436px;border:3px solid var(--line)}
.photo-card{position:absolute;left:112px;top:-84px;width:387px;height:551px;background:#fff;padding:12px;box-shadow:0 4px 14px rgba(0,0,0,.12)}
.photo-card .photo{position:static;width:100%;height:100%;background:linear-gradient(160deg,#7d8a54 0%,#5a4a2c 45%,#6f6a55 100%)}
.about-copy{position:absolute;left:607px;top:72px;width:480px}
.about-copy h2{font-family:"Roboto Slab",serif;font-weight:700;font-size:35px;line-height:40px;color:var(--ink)}
.about-copy p{font-size:13.5px;line-height:30px;color:var(--text);margin:21px 0 16px}

/* adopt */
.section-title{position:absolute;left:0;width:1200px;text-align:center;font-family:"Roboto Slab",serif;font-weight:700;color:var(--ink)}
.adopt-lead{position:absolute;left:0;top:1282px;width:1200px;text-align:center;font-size:14px;line-height:30px}
.filter{position:absolute;top:1364px;height:43px;border-radius:22px;display:flex;align-items:center;justify-content:center;font-family:"Roboto Slab",serif;font-weight:700;font-size:15px;background:var(--gold);color:var(--ink);white-space:nowrap}
.filter.active{background:#fff;border:2px solid var(--red);color:var(--red)}
.horse{position:absolute;width:315px;height:290px}
.horse-info{position:absolute;left:443px;top:1463px;width:315px;height:290px;background:linear-gradient(180deg,#2a241c,#1a1712);color:#fff;padding:70px 36px 0}
.horse-info h3{text-align:center;font-family:"Roboto Slab",serif;font-weight:500;font-size:22px;margin-bottom:14px}
.horse-info dl{font-size:14px;line-height:26px;white-space:nowrap}
.horse-info b{font-weight:700;margin-right:12px}

/* give */
.give{position:absolute;left:0;top:2147px;width:1200px;height:424px;background:linear-gradient(90deg,#4b3220 0%,#6b5237 28%,#3c4a2a 50%,#4f6a2c 75%,#6a8a38 100%)}
.give-copy{position:absolute;left:659px;top:88px;width:460px;color:#fff}
.give-copy h2{font-family:"Roboto Slab",serif;font-weight:700;font-size:36px;line-height:46px}
.give-copy p{font-size:13.5px;line-height:30px;margin:8px 0 20px 2px}

/* contact */
.info-item{position:absolute;left:112px;display:flex;gap:10px}
.info-item .ring{width:44px;height:44px;border:2px solid var(--red);border-radius:50%;display:flex;align-items:center;justify-content:center;flex:none}
.info-item .ring svg{width:16px;height:16px}
.info-item h4{color:var(--red);font-weight:600;font-size:14px;margin-bottom:3px}
.info-item p{font-size:14px;line-height:24px;color:var(--ink)}
.field{position:absolute;background:#fff;box-shadow:0 1px 6px rgba(0,0,0,.16);font-size:14px;color:#666;padding:11px 15px}
.check{position:absolute;left:417px;top:3004px;width:278px;height:73px;background:#f9f9f9;border:1px solid #d3d3d3;box-shadow:0 1px 4px rgba(0,0,0,.1);display:flex;align-items:center;padding-left:20px;gap:14px;font-size:14px;font-weight:600;color:var(--ink)}
.check .box{width:27px;height:27px;border:2px solid #c1c1c1;border-radius:3px;background:#fff}
.check .badge{position:absolute;right:0;top:0;width:78px;height:71px;background:#ececec}
.submit{position:absolute;left:420px;top:3092px;width:136px;height:41px;border-radius:21px;background:var(--red);color:#fff;font-family:"Roboto Slab",serif;font-weight:700;font-size:15px;display:flex;align-items:center;justify-content:center;gap:12px}

/* footer */
.footer{position:absolute;left:0;top:3220px;width:1200px;height:398px;background:var(--footer);color:#fff}
.footer .brand{left:106px;top:66px;width:180px;font-size:19px;line-height:25px}
.socials{position:absolute;left:112px;top:246px;display:flex;gap:12px}
.socials span{width:38px;height:38px;border-radius:50%;background:var(--red)}
.fcol{position:absolute;top:58px}
.fcol h5{font-family:"Roboto Slab",serif;font-weight:700;font-size:19px;margin-bottom:14px;white-space:nowrap}
.fcol li{list-style:none;font-size:14px;line-height:32px;padding-left:4px;white-space:nowrap}
.fcontact{display:flex;gap:8px;font-size:14px;line-height:22px;margin-bottom:14px}
.fcontact svg{width:18px;height:18px;flex:none;margin-top:2px}
.footer hr{position:absolute;left:0;top:320px;width:1200px;border:0;border-top:1px solid #333}
.copy{position:absolute;left:0;top:346px;width:1200px;text-align:center;font-size:14px}
</style>
</head>
<body>

<header class="hero">
  <div class="photo" role="img" aria-label="Smiling woman standing beside a chestnut horse wearing a bridle" style="inset:0;background:linear-gradient(100deg,rgba(20,14,10,.65) 0%,rgba(20,14,10,.25) 45%,rgba(0,0,0,0) 70%)"></div>
  <div class="brand">FERNVALE<br>QUILLSTONE<br>HERITAGE<br>SOCIETY</div>
  <div class="topbar">
    <svg viewBox="0 0 16 16"><rect x="1" y="3" width="14" height="10" fill="none" stroke="#d3232f" stroke-width="1.6"/><path d="M1 3l7 6 7-6" fill="none" stroke="#d3232f" stroke-width="1.6"/></svg>
    <span>Sed ut perspiciatis unde omnis</span>
    <svg viewBox="0 0 16 16" style="margin-left:16px"><path d="M3 1l3 3-2 2c1 2 3 4 5 5l2-2 3 3-2 3C7 15 1 9 1 3z" fill="#d3232f"/></svg>
    <span>188-888-8888</span>
    <span class="dot"></span><span class="dot"></span><span class="dot"></span><span class="dot"></span>
  </div>
  <nav class="nav">
    <span>HOME</span><span>ABOUT</span><span>ADOPT</span><span>HORSES</span><span>DONATE/SHOP</span><span>CONTACT</span>
    <svg width="14" height="14" viewBox="0 0 16 16"><circle cx="6.5" cy="6.5" r="4.5" fill="none" stroke="#fff" stroke-width="2.2"/><path d="M10 10l5 5" stroke="#fff" stroke-width="2.4"/></svg>
    <svg width="14" height="14" viewBox="0 0 16 16"><path d="M1 2h14M1 6h14M1 10h14M1 14h14" stroke="#fff" stroke-width="2"/></svg>
  </nav>
  <div class="hero-copy">
    <h1>Retire Retrain Rehome</h1>
    <p>We support and develop retired thoroughbred racehorses for their next chapter in life</p>
    <a class="btn">LEARN MORE <svg viewBox="0 0 16 16"><circle cx="8" cy="8" r="8" fill="#1c1c1c"/><path d="M6 4l4 4-4 4" stroke="#f1b25c" stroke-width="2" fill="none"/></svg></a>
  </div>
</header>

<section class="about">
  <div class="outline-frame"></div>
  <div class="photo-card"><div class="photo" role="img" aria-label="Woman kneeling in a pasture greeting a young brown horse"></div></div>
  <div class="about-copy">
    <h2>WHAT IS THOROUGHBRED AFTERCARE?</h2>
    <p>The health, safety and welfare of our equine athletes does not end at the finish line, and retirement and aftercare are critical to the success of the racing industry. Aftercare is the safe placement of racehorses after their careers as racehorses are completed. Some horses might retire to the breeding shed or broodmare</p>
    <a class="btn">LEARN MORE <svg viewBox="0 0 16 16"><circle cx="8" cy="8" r="8" fill="#1c1c1c"/><path d="M6 4l4 4-4 4" stroke="#f1b25c" stroke-width="2" fill="none"/></svg></a>
  </div>
</section>

<h2 class="section-title" style="top:1226px;font-size:35px">ADOPT A HORSE</h2>
<p class="adopt-lead">Fernvale Quillstone Heritage Society is committed to helping match you<br>with the perfect horse.</p>
<div class="filter active" style="left:365px;width:87px">ALL</div>
<div class="filter" style="left:468px;width:176px">THOROUGHBREDS</div>
<div class="filter" style="left:660px;width:175px">STANDARDBREDS</div>

<div class="horse" role="img" aria-label="Black horse with long mane standing in a paddock" style="left:112px;top:1463px;background:linear-gradient(180deg,#8fb0c8 0%,#5d7a3e 45%,#2a221c 70%,#8aa047 100%)"></div>
<div class="horse-info">
  <h3>COPPER WREN</h3>
  <dl>
    <div><b>FEE</b> $500 NOW $300 UNTIL 5/31</div>
    <div><b>BIRTH YEAR</b> 2021 &nbsp;COLOR &nbsp;&nbsp;&nbsp; BAY</div>
    <div><b>GENDER</b> Gelding</div>
    <div><b>LOCATION</b> LEXINGTON, KY</div>
  </dl>
</div>
<div class="horse" role="img" aria-label="Dark bay horse standing on a lawn" style="left:773px;top:1463px;background:linear-gradient(180deg,#2f4a2a 0%,#3d2a1d 50%,#5f9a3a 100%)"></div>
<div class="horse" role="img" aria-label="Dark bay horse posed in front of trees" style="left:112px;top:1768px;background:linear-gradient(180deg,#2e3f23 0%,#2a1f18 55%,#6e9a3e 100%)"></div>
<div class="horse" role="img" aria-label="Bay horse cantering in a field" style="left:443px;top:1768px;background:linear-gradient(180deg,#b7c9a3 0%,#7a4a28 55%,#6c8f3a 100%)"></div>
<div class="horse" role="img" aria-label="Chestnut horse standing before hills" style="left:773px;top:1768px;background:linear-gradient(180deg,#7d8c74 0%,#7b4c2c 55%,#6d9a32 100%)"></div>

<section class="give">
  <div class="photo" role="img" aria-label="Rider in a riding helmet looking at her brown horse" style="left:0;top:0;width:640px;height:424px;background:linear-gradient(90deg,rgba(60,38,22,.6),rgba(30,30,40,.2))"></div>
  <div class="give-copy">
    <h2>Make a Difference</h2>
    <p>Lorem ipsum dolor sit amet, consectetur adipiscing elit, sed do eiusmod tempor incididunt ut labore et dolore magna aliqua. Quis ipsum suspendisse ultrices gravida. Risus commodo viverra maecenas accumsan lacus vel facilisis.</p>
    <a class="btn">MORE WAYS TO GIVE <svg viewBox="0 0 16 16"><circle cx="8" cy="8" r="8" fill="#1c1c1c"/><path d="M6 4l4 4-4 4" stroke="#f1b25c" stroke-width="2" fill="none"/></svg></a>
  </div>
</section>

<h2 class="section-title" style="top:2650px;font-size:33px">HAVE A QUESTION OR NEED MORE INFORMATION?</h2>

<div class="info-item" style="top:2744px">
  <div class="ring"><svg viewBox="0 0 16 16"><path d="M8 1a5 5 0 0 0-5 5c0 4 5 9 5 9s5-5 5-9a5 5 0 0 0-5-5z" fill="#ad1a26"/><circle cx="8" cy="6" r="2" fill="#fff"/></svg></div>
  <div><h4>LOCATION</h4><p>Lorem ipsum dolor sit amet,<br>consectetur adipiscing elit,<br>sed do</p></div>
</div>
<div class="info-item" style="top:2864px">
  <div class="ring"><svg viewBox="0 0 16 16"><path d="M3 1l3 3-2 2c1 2 3 4 5 5l2-2 3 3-2 3C7 15 1 9 1 3z" fill="#ad1a26"/></svg></div>
  <div><h4>CALL US</h4><p>1888-888-888</p></div>
</div>
<div class="info-item" style="top:2944px">
  <div class="ring"><svg viewBox="0 0 16 16"><rect x="1" y="3" width="14" height="10" fill="#ad1a26"/><path d="M1 3l7 6 7-6" fill="none" stroke="#fff" stroke-width="1.4"/></svg></div>
  <div><h4>EMAIL US</h4><p>hello@fernvalequillstone.org</p></div>
</div>

<div class="field" style="left:417px;top:2740px;width:325px;height:38px">First Name</div>
<div class="field" style="left:761px;top:2740px;width:325px;height:38px">Last Name</div>
<div class="field" style="left:417px;top:2796px;width:325px;height:38px">Your Phone</div>
<div class="field" style="left:761px;top:2796px;width:325px;height:38px">Your Email</div>
<div class="field" style="left:417px;top:2855px;width:669px;height:132px">How Can we help you?</div>
<div class="check"><span class="box"></span>I'm not a robot<span class="badge"></span></div>
<div class="submit">SUBMIT <svg width="16" height="16" viewBox="0 0 16 16"><path d="M1 8l14-7-4 14-3-5z" fill="#fff"/></svg></div>

<footer class="footer">
  <div class="brand">FERNVALE<br>QUILLSTONE<br>HERITAGE<br>SOCIETY</div>
  <div class="socials"><span></span><span></span><span></span><span></span></div>
  <div class="fcol" style="left:348px"><h5>QUICK LINK</h5><ul><li>Home</li><li>About</li><li>Adopt horse</li><li>Donate/shop</li><li>Contact</li></ul></div>
  <div class="fcol" style="left:556px"><h5>HELP LINK</h5><ul><li>Terms&amp;condtions</li><li>Privacy</li><li>Policy</li><li>About Us</li><li>Support</li></ul></div>
  <div class="fcol" style="left:783px;width:320px"><h5>CONTACT US</h5>
    <div class="fcontact"><svg viewBox="0 0 16 16"><path d="M8 1a5 5 0 0 0-5 5c0 4 5 9 5 9s5-5 5-9a5 5 0 0 0-5-5z" fill="#fff"/><circle cx="8" cy="6" r="2" fill="#1e1e1e"/></svg><span>Lorem ipsum dolor<br>sit amet</span></div>
    <div class="fcontact"><svg viewBox="0 0 16 16"><path d="M3 1l3 3-2 2c1 2 3 4 5 5l2-2 3 3-2 3C7 15 1 9 1 3z" fill="#fff"/></svg><span>188-888-8888</span></div>
    <div class="fcontact"><svg viewBox="0 0 16 16"><rect x="1" y="3" width="14" height="10" fill="none" stroke="#fff" stroke-width="1.4"/><path d="M1 3l7 6 7-6" fill="none" stroke="#fff" stroke-width="1.4"/></svg><span>info@fernvalequillstone.org</span></div>
  </div>
  <hr>
  <p class="copy">© 2021 Fernvale Quillstone Heritage Society All Rights Reserved</p>
</footer>

</body>
</html>
```